Business card for Eyelash extension salon in Beverly Hills,California USA

We need new business card for our salon in Beverly Hills. The salon name is 'Lashvera' . We would like to have...Business name: Lashvera Name of person: will provide later Address 4720 N.Alder Crest Ave Cedar Heights , OR 97455 Phone: will provide later (Text only) Web: www.lashverastudio.example Snapgrid icon, Circlebook icon follow us for seasonal campaign and news @lashverastudiolounge Design should look elegant, high-end, clean, simple, cohesive with my brand. Please refer my brand board. Business name color will be metallic bronzy color. Im thinking grey background or white background. Thanks

Target Market(s)

25-35. Gender neutral. People who are in Entertainment business industry.
This is High-end Eyelash extension salon in Beverly Hills

Industry/Entity Type

Beauty Salon

Contact Information for Business Card

Business name: Lashvera
Name of person: will provide later
Address 4720 N.Alder Crest Ave Cedar Heights , OR 97455
Phone: will provide later (Text only)
Web: www.lashverastudio.example
Snapgrid icon, Circlebook icon
follow us for seasonal campaign and news @lashverastudiolounge

Requirements
Must have
• Beautiful, elegant, clean and simple look but very attractive and modern
Should not have
• We don't like too clutter, too busy designs.

```html
<!DOCTYPE html>
<html lang="en">
<head>
<meta charset="utf-8">
<title>Lashvera Business Card</title>
<link href="https://fonts.googleapis.com/css2?family=Playfair+Display:wght@400&family=Work+Sans:wght@400;500&display=swap" rel="stylesheet">
<style>
  :root {
    --backdrop: #2a2a2c;
    --card: #0a0b0d;
    --bronze: #a7744f;
    --bronze-soft: #8a6244;
  }
  * { margin: 0; padding: 0; box-sizing: border-box; }
  html, body { width: 1200px; height: 800px; overflow: hidden; }
  body {
    background: var(--backdrop);
    font-family: "Work Sans", Arial, sans-serif;
    color: var(--bronze);
    position: relative;
  }
  .card {
    position: absolute;
    top: 248px;
    width: 530px;
    height: 303px;
    background: var(--card);
    border-radius: 14px;
    overflow: hidden;
  }
  .card--front { left: 50px; }
  .card--back { left: 620px; }

  .brand-name {
    position: absolute;
    right: 48px;
    top: 100px;
    font-family: "Playfair Display", Georgia, serif;
    font-size: 62px;
    font-weight: 400;
    line-height: 1.2;
    color: var(--bronze);
  }
  .social {
    position: absolute;
    left: 40px;
    bottom: 34px;
    display: flex;
    align-items: center;
    gap: 12px;
    font-size: 13px;
    font-weight: 500;
    line-height: 16px;
    color: var(--bronze);
    white-space: nowrap;
  }
  .social__network { display: flex; align-items: center; gap: 5px; }
  .social__dot { width: 7px; height: 7px; border-radius: 50%; background: var(--bronze); }

  .person-name {
    position: absolute;
    left: 34px;
    top: 36px;
    font-family: "Playfair Display", Georgia, serif;
    font-size: 22px;
    font-weight: 400;
    line-height: 28px;
    letter-spacing: 1px;
    color: var(--bronze);
  }
  .person-role {
    position: absolute;
    left: 36px;
    top: 70px;
    font-size: 10px;
    font-weight: 500;
    letter-spacing: 1.6px;
    color: var(--bronze);
  }
  .web-vertical {
    position: absolute;
    right: 20px;
    top: 24px;
    writing-mode: vertical-rl;
    transform: rotate(180deg);
    font-size: 11px;
    letter-spacing: 1px;
    color: var(--bronze);
  }
  .divider {
    position: absolute;
    top: 180px;
    left: 250px;
    right: 0;
    height: 1px;
    background: var(--bronze-soft);
  }
  .divider-dash {
    position: absolute;
    top: 196px;
    left: 0;
    width: 16px;
    height: 1px;
    background: var(--bronze-soft);
  }
  .contact {
    position: absolute;
    left: 50px;
    top: 186px;
    font-size: 13px;
    line-height: 18px;
    color: var(--bronze-soft);
    white-space: nowrap;
  }
  .contact__label { display: inline-block; width: 26px; }
  .address {
    position: absolute;
    right: 28px;
    top: 196px;
    font-size: 10px;
    font-weight: 500;
    color: var(--bronze);
    white-space: nowrap;
  }
  .card--back .social { left: 52px; bottom: 30px; }
</style>
</head>
<body>
  <section class="card card--front">
    <h1 class="brand-name">Lashvera</h1>
    <div class="social">
      <span class="social__network"><span class="social__dot"></span>Snapgrid</span>
      <span class="social__network">Circlebook</span>
      <span class="social__handle">@lashverastudiolounge</span>
    </div>
  </section>

  <section class="card card--back">
    <h2 class="person-name">MARISOL DENVALE</h2>
    <p class="person-role">WEEDING PLANNER</p>
    <p class="web-vertical">lashverastudio.example</p>
    <div class="divider"></div>
    <div class="divider-dash"></div>
    <div class="contact">
      <p><span class="contact__label">T</span>555-014-2297</p>
      <p><span class="contact__label">E</span>hello@lashvera.example</p>
    </div>
    <p class="address">4720 N.Alder Crest Ave Cedar Heights , OR 97455</p>
    <div class="social">
      <span class="social__network"><span class="social__dot"></span>Snapgrid</span>
      <span class="social__network">Circlebook</span>
      <span class="social__handle">@lashvera</span>
    </div>
  </section>
</body>
</html>
```